Company Mission & Values Poster

I'd like an A2 Portrait Poster displaying our company's Mission & Values.
See our website for our logo, fonts, mission & values.
https://valdintor.com.au/

Our Mission: Creating homes for abundant life
Values: Love, Thinking, Team, Zoe.

Some ideas to consider:
Mission as the Headline then
A logo for each of the 4 Values and the words

Target Market(s)

Myself & my team

Industry/Entity Type

Real Estate

Font styles to use
Other font styles liked:
• Company fonts as seen on our website

```html
<!DOCTYPE html>
<html lang="en">
<head>
<meta charset="utf-8">
<title>Valdintor — Mission &amp; Values Poster</title>
<link rel="stylesheet" href="https://fonts.googleapis.com/css2?family=Bodoni+Moda:opsz,wght@6..96,400&family=Cormorant+Garamond:wght@500;600&display=swap">
<style>
  :root {
    --page: #ffffff;
    --stone: #dad8cf;
    --sage: #a7b38b;
    --leaf: #578357;
    --forest: #3c5e43;
    --ink: #1f3a2d;
    --display: "Bodoni Moda", "Didot", serif;
    --text: "Cormorant Garamond", "Garamond", serif;
  }
  html, body {
    margin: 0;
    padding: 0;
    width: 932px;
    height: 1200px;
    overflow: hidden;
    background: var(--page);
  }
  .poster {
    position: absolute;
    left: 118px;
    top: 108px;
    width: 693px;
    height: 980px;
    display: block;
  }
  .value-word {
    font-family: var(--display);
    font-weight: 400;
    font-size: 250px;
  }
  .value-word--light { fill: var(--stone); }
  .value-word--dark { fill: var(--forest); }
  .mission {
    font-family: var(--text);
    font-weight: 500;
    font-size: 74px;
    letter-spacing: 3px;
    fill: var(--stone);
  }
  .brand-name {
    font-family: var(--text);
    font-weight: 600;
    font-size: 78px;
    letter-spacing: 12px;
    fill: var(--ink);
  }
</style>
</head>
<body>
<svg class="poster" viewBox="216 198 1264 1787" xmlns="http://www.w3.org/2000/svg" aria-label="Valdintor mission and values poster">
  <defs>
    <clipPath id="poster-area">
      <rect x="216" y="198" width="1264" height="1787"/>
    </clipPath>
    <path id="arc-love" d="M388 393 A460 460 0 0 0 1308 393"/>
    <path id="arc-thinking" d="M198 393 A650 650 0 0 0 1498 393"/>
    <path id="arc-team" d="M-12 393 A860 860 0 0 0 1708 393"/>
    <path id="arc-zoe" d="M-217 393 A1065 1065 0 0 0 1913 393"/>
  </defs>

  <g clip-path="url(#poster-area)">
    <rect class="backdrop" x="216" y="198" width="1264" height="1787" fill="var(--stone)"/>
    <circle class="ring ring--outer" cx="848" cy="393" r="860" fill="var(--sage)"/>
    <circle class="ring ring--middle" cx="848" cy="393" r="659" fill="var(--leaf)"/>
    <circle class="ring ring--inner" cx="848" cy="393" r="457" fill="var(--forest)"/>

    <text class="mission" text-anchor="middle">
      <tspan x="850" y="395">Creating homes for</tspan>
      <tspan x="850" y="478">abundant life</tspan>
    </text>

    <text class="value-word value-word--light">
      <textPath href="#arc-love" startOffset="241" textLength="506" lengthAdjust="spacingAndGlyphs">Love</textPath>
    </text>
    <text class="value-word value-word--light">
      <textPath href="#arc-thinking" startOffset="556" textLength="941" lengthAdjust="spacingAndGlyphs">Thinking</textPath>
    </text>
    <text class="value-word value-word--dark">
      <textPath href="#arc-team" startOffset="1156" textLength="594" lengthAdjust="spacingAndGlyphs">Team</textPath>
    </text>
    <text class="value-word value-word--dark">
      <textPath href="#arc-zoe" startOffset="1749" textLength="457" lengthAdjust="spacingAndGlyphs">Zoe</textPath>
    </text>

    <text class="brand-name" x="850" y="1826" text-anchor="middle">VALDINTOR</text>
  </g>
</svg>
</body>
</html>
```